We are a recruitment company based in Norwich/Cambridge England.
I have included our company logo which we want to remain the same.

What we are looking for is a new creative Business card which will really stand out!!

Contact Information for Business Card

Harriet Dunmore
email: Harriet@plavex.co.uk
Address: Brackwell House
Fenmoor Enterprise Park
Partridge Way
Norwich
QB9 3KX
Tel:01632 960418

```html
<!DOCTYPE html>
<html lang="en">
<head>
<meta charset="utf-8">
<title>Plavex business card</title>
<link href="https://fonts.googleapis.com/css2?family=Lato:wght@300;400;700&display=swap" rel="stylesheet">
<style>
  :root {
    --green: #7dc242;
    --green-light: #8fd04f;
    --grey: #8e8c91;
    --grey-text: #6f6f73;
    --ink: #4a4a4e;
    --white: #ffffff;
    --stage: #ecebe8;
  }
  * { margin: 0; padding: 0; box-sizing: border-box; }
  html, body { width: 1200px; height: 886px; overflow: hidden; }
  body {
    background: var(--stage);
    font-family: "Lato", Arial, sans-serif;
    position: relative;
  }
  .card {
    position: absolute;
    top: 283px;
    width: 540px;
    height: 320px;
    border-radius: 22px;
    overflow: hidden;
    box-shadow: 0 6px 18px rgba(0,0,0,0.12);
  }
  .card-front { left: 45px; background: var(--white); }
  .card-back  { left: 615px; background: var(--green); }

  /* front */
  .front-base { position: absolute; inset: 0; }
  .brand {
    position: absolute;
    display: flex;
    align-items: center;
    gap: 10px;
  }
  .brand-dot {
    width: 34px; height: 34px; border-radius: 50%;
    background: var(--green);
  }
  .brand-name {
    font-weight: 700;
    font-size: 38px;
    letter-spacing: -0.5px;
    line-height: 1;
  }
  .brand-tagline {
    font-size: 9px;
    letter-spacing: 2.4px;
    color: var(--grey-text);
    margin-top: 4px;
  }
  .card-front .brand { left: 40px; top: 120px; }
  .card-front .brand-name { color: var(--ink); }
  .card-front .brand-tagline { margin-left: 44px; }

  .divider {
    position: absolute;
    left: 272px; top: 46px;
    width: 1px; height: 170px;
    background: #d6d6d6;
  }
  .contact { position: absolute; left: 296px; top: 42px; color: var(--ink); }
  .contact-name {
    font-size: 21px; font-weight: 400; color: var(--green);
    text-transform: uppercase; letter-spacing: 0.3px;
  }
  .contact-role {
    font-size: 13px; font-weight: 300; color: var(--grey-text);
    text-transform: uppercase; margin-bottom: 10px;
  }
  .contact-address { font-size: 12px; font-weight: 400; line-height: 1.35; margin-bottom: 8px; }
  .contact-list { list-style: none; font-size: 12px; line-height: 1.45; }
  .contact-list li { display: flex; align-items: center; gap: 7px; }
  .contact-list svg { width: 11px; height: 11px; flex: none; }

  .website {
    position: absolute;
    right: 34px; bottom: 34px;
    font-size: 12px; letter-spacing: 5px;
    color: var(--grey-text);
  }

  /* back */
  .back-texture { position: absolute; inset: 0; }
  .card-back .brand {
    left: 50%; top: 50%;
    transform: translate(-50%, -50%);
  }
  .card-back .brand-dot { background: var(--white); width: 46px; height: 46px; }
  .card-back .brand-name { color: var(--white); font-size: 52px; }
  .card-back .brand-tagline { color: var(--white); margin-left: 58px; font-size: 10px; }
  .back-web {
    position: absolute; left: 40px; bottom: 26px;
    font-size: 11px; letter-spacing: 5px; color: var(--white);
  }
</style>
</head>
<body>

<section class="card card-front" aria-label="Business card front">
  <svg class="front-base" width="540" height="320" viewBox="0 0 540 320" aria-hidden="true">
    <rect x="0" y="300" width="540" height="20" fill="var(--green)"/>
    <path d="M0 258 H150 Q176 258 190 280 L205 300 V320 H0 Z" fill="var(--green)"/>
    <path d="M0 266 H146 Q168 266 180 285 L190 300 V320 H0 Z" fill="var(--grey)"/>
    <rect x="190" y="300" width="350" height="6" fill="var(--green-light)"/>
  </svg>

  <div class="brand">
    <span class="brand-dot"></span>
    <div>
      <div class="brand-name">Plavex</div>
      <div class="brand-tagline">Technology Recruitment</div>
    </div>
  </div>

  <div class="divider"></div>

  <div class="contact">
    <p class="contact-name">Harriet Dunmore</p>
    <p class="contact-role">CEO/Founder</p>
    <p class="contact-address">Brackwell House<br>Fenmoor Enterprise Park<br>Partridge Way, Norwich QB9 3KX</p>
    <ul class="contact-list">
      <li>
        <svg viewBox="0 0 12 12"><path d="M2.5 1 L4.5 1 L5.3 3.6 L4 4.6 Q5 6.8 7.4 8 L8.4 6.7 L11 7.5 L11 9.5 Q10.5 11 9 11 Q2 9.8 1 3 Q1 1.5 2.5 1 Z" fill="var(--green)"/></svg>
        01632 960418
      </li>
      <li>
        <svg viewBox="0 0 12 12"><rect x="3" y="0.5" width="6" height="11" rx="1" fill="none" stroke="var(--green)" stroke-width="1.3"/><rect x="5" y="9" width="2" height="1" fill="var(--green)"/></svg>
        01632 960527
      </li>
      <li>
        <svg viewBox="0 0 12 12"><rect x="1" y="4" width="10" height="7" rx="1" fill="var(--green)"/><rect x="3" y="1" width="6" height="3" fill="none" stroke="var(--green)" stroke-width="1.2"/></svg>
        01632 960733
      </li>
      <li>
        <svg viewBox="0 0 12 12"><rect x="0.8" y="2" width="10.4" height="8" rx="1" fill="var(--green)"/><path d="M1.5 3 L6 6.5 L10.5 3" fill="none" stroke="var(--white)" stroke-width="1"/></svg>
        Harriet@plavex.co.uk
      </li>
    </ul>
  </div>

  <p class="website">www.plavex.co.uk</p>
</section>

<section class="card card-back" aria-label="Business card back">
  <svg class="back-texture" width="540" height="320" viewBox="0 0 540 320" role="img" aria-label="Faint repeating brand pattern across the green background">
    <defs>
      <radialGradient id="backGlow" cx="50%" cy="45%" r="70%">
        <stop offset="0" stop-color="#8bcc4d"/>
        <stop offset="1" stop-color="#76bb3c"/>
      </radialGradient>
    </defs>
    <rect width="540" height="320" fill="url(#backGlow)"/>
  </svg>

  <div class="brand">
    <span class="brand-dot"></span>
    <div>
      <div class="brand-name">Plavex</div>
      <div class="brand-tagline">Technology Recruitment</div>
    </div>
  </div>

  <p class="back-web">.co.uk</p>
</section>

</body>
</html>
```